Industry / Entity Type

Financial consultancy / advisers

Current site is: http://www.brightmoor-counsel.com

Looking for a complete overhaul of this site, we are after a clean modern look. Will require the ability to easily add, update and remove content, hence the WordPress design.
Example:
Add case studies
Industry documentation (downloadable brochures / flyers and such)

What we like from our current site is the colour the fonts and the logo (the city of London) we would like to have other city outlines (NYC and Tokyo, Hong Kong, Singapore).

The site will be used by our potential clients to get in contact and re-view the case studies, if possible would like to have a client login area where they can download our documents like NDA’s etc and T&C’s.

Task Outline

Create a Web Design (Coded - Design and coding required)
Designer must provide full implementation/coding depending on the platform chosen by the client (i.e. WordPress theme, HTML/CSS, bootstrap etc.)

Task Description

I need a full website built that must work on desktop and mobile. I can provide the London city skyline and the font file, which we have used. Some stock industrial photos will be required.

Requirements:

*Splash page
*What We Do
*How We do it
*Who Are We? To have the same information and links as the current site
*Why use us?
*Clients: To have the same information and links as the current site
*Partners: To have the same information and links as the current site
*Contact:

Target Market(s)

Financial institutions trading Equities, Futures, Options, Forex and Fixed Income.
Regulators, Exchanges, ECN’s
Buy side firms and Sell side firms

Industry/Entity Type

Financial

Coding

Coded - Design and coding required

Number of Pages Required

5+ page

Font styles to use
Sans Serif

Colors
f04a50

Requirements
Must have
• Splash page
• What We Do
• How We do it
• Who Are We? To have the same information and links as the current site
• Why use us?
• Clients: To have the same information and links as the current site
• Partners: To have the same information and links as the current site
• Contact:

```html
<!DOCTYPE html>
<html lang="en">
<head>
<meta charset="utf-8">
<title>Brightmoor Counsel — Interim Management</title>
<link rel="stylesheet" href="https://fonts.googleapis.com/css2?family=Open+Sans:wght@400;600;700&family=Oswald:wght@400;500;600&family=Michroma&display=swap">
<style>
:root{
  --brand:#f04a50;
  --brand-deep:#8e1c22;
  --brand-dark:#6e1216;
  --ink:#333;
  --muted:#777;
  --line:#e3e3e3;
  --paper:#fff;
  --logo-ink:#2d3a5a;
}
*{box-sizing:border-box;margin:0;padding:0}
html,body{width:1200px;height:3240px;overflow:hidden;background:var(--paper)}
body{font-family:"Open Sans",Arial,sans-serif;color:var(--ink);position:relative}

.topbar{height:32px;background:var(--brand-deep);color:#fff;display:flex;align-items:center;justify-content:space-between;padding:0 60px;font-size:11px}
.topbar .links{display:flex;gap:22px}
.topbar .actions{display:flex;gap:16px;align-items:center}
.topbar .login{border:1px solid #fff;padding:3px 10px;font-size:10px;letter-spacing:1px}

.masthead{height:108px;display:flex;flex-direction:column;align-items:center;justify-content:center}
.brand-mark{display:flex;align-items:center;gap:10px}
.brand-mark .dot{width:14px;height:14px;background:var(--brand);border-radius:50%}
.brand-mark .name{font-family:"Oswald",sans-serif;font-size:26px;letter-spacing:4px;color:var(--ink);text-transform:uppercase}
.brand-rule{width:300px;height:2px;background:var(--brand);margin-top:8px}

.mainnav{height:40px;display:flex;justify-content:center;gap:46px;align-items:center;border-bottom:1px solid var(--line)}
.mainnav a{font-family:"Oswald",sans-serif;font-size:15px;color:var(--brand);text-decoration:none;letter-spacing:1px}

.hero{position:relative;height:480px}
.hero-photo{position:absolute;inset:0;background:linear-gradient(180deg,#b9c2c9 0%,#8a8f94 45%,#5a4a44 75%,#3a2b28 100%)}
.hero-copy{position:absolute;left:0;right:0;top:110px;text-align:center;color:#fff}
.hero-copy .band{display:inline-block;background:rgba(142,28,34,.55);padding:10px 40px}
.hero-copy h1{font-family:"Oswald",sans-serif;font-weight:500;font-size:52px;letter-spacing:3px}
.hero-copy p{font-family:"Oswald",sans-serif;font-size:34px;letter-spacing:2px;line-height:1.5;margin-top:14px}
.hero-dots{position:absolute;bottom:22px;left:0;right:0;display:flex;justify-content:center;gap:10px}
.hero-dots span{width:10px;height:10px;border-radius:50%;background:rgba(255,255,255,.6)}
.hero-dots span.on{background:var(--brand)}

.cities{height:140px;display:flex;justify-content:center;gap:70px;align-items:center;border-bottom:1px solid var(--line)}
.city{width:200px;text-align:center}
.city .skyline{height:60px;background:linear-gradient(180deg,#fff 0%,#e6e6e6 100%);border-bottom:2px solid #999}
.city .label{font-family:"Michroma",sans-serif;font-size:18px;color:#555;margin-top:8px;letter-spacing:2px}

.intro{text-align:center;padding:36px 140px 0;height:200px}
.intro h2{font-family:"Oswald",sans-serif;font-weight:500;color:var(--brand);font-size:30px;line-height:1.3;letter-spacing:1px}
.intro p{font-size:12px;color:var(--muted);line-height:1.7;margin-top:18px}

.feature{display:flex;gap:40px;padding:20px 140px 0;align-items:flex-start}
.feature .art{flex:0 0 200px;height:200px;border-radius:50%;background:radial-gradient(circle,#f04a50 0%,#c6282e 60%,#fff 61%)}
.feature .art.figure{border-radius:0;background:linear-gradient(180deg,#3a5f9a,#f04a50)}
.feature h3{font-family:"Michroma",sans-serif;font-size:22px;color:var(--brand);margin-top:20px}
.feature h4{font-size:14px;font-weight:700;color:var(--ink);margin-top:10px;line-height:1.5}
.feature p{font-size:12px;color:var(--muted);line-height:1.7;margin-top:12px}
.feature .lines{font-size:16px;color:var(--ink);margin-top:14px;line-height:1.7}
.feature .mifid-title{font-family:"Michroma",sans-serif;font-size:32px;color:var(--brand)}

.band-title{height:60px;background:var(--brand-deep);color:#fff;display:flex;align-items:center;justify-content:center;font-family:"Oswald",sans-serif;font-size:26px;letter-spacing:2px}

.logo-grid{display:flex;flex-wrap:wrap;justify-content:center;align-content:center;gap:40px 30px;padding:0 100px}
.logo{display:flex;align-items:center;justify-content:center;gap:8px;font-weight:700;font-size:17px;color:var(--logo-ink);width:220px;height:60px;white-space:nowrap}
.logo .sq{width:14px;height:14px;background:var(--brand);flex:none}
.logo .ci{width:14px;height:14px;border-radius:50%;background:var(--logo-ink);flex:none}

.team{display:flex;justify-content:center;gap:120px;padding-top:40px}
.member{width:240px;text-align:center}
.member .photo{height:240px;background:linear-gradient(180deg,#d9d4cf,#9a948e)}
.member h5{font-family:"Oswald",sans-serif;font-weight:500;font-size:20px;margin-top:20px;letter-spacing:1px}
.member p{font-size:11px;color:var(--muted);line-height:1.6;margin-top:4px}

.footer{position:absolute;left:0;right:0;bottom:0;height:140px;background:var(--brand-dark);color:#fff;text-align:center;padding-top:18px}
.footer .social{display:flex;justify-content:center;gap:14px}
.footer .social span{width:28px;height:20px;background:var(--brand);border-radius:3px}
.footer nav{display:flex;justify-content:center;gap:40px;margin-top:26px;font-size:12px}
.footer small{display:block;margin-top:26px;font-size:10px;color:#e8c9ca}
</style>
</head>
<body>

<header>
  <div class="topbar">
    <div class="links"><span>Welcome</span><span>Blog</span><span>Search</span></div>
    <div class="actions"><span>+44 20 7946 0183</span><span class="login">CLIENT LOGIN</span></div>
  </div>
  <div class="masthead">
    <div class="brand-mark"><span class="dot"></span><span class="name">Brightmoor Counsel</span></div>
    <div class="brand-rule"></div>
  </div>
  <nav class="mainnav">
    <a href="#">HOME</a><a href="#">WHAT WE DO</a><a href="#">HOW WE DO IT</a><a href="#">WHO ARE WE</a><a href="#">WHY USE US</a><a href="#">CLIENTS</a><a href="#">PARTNERS</a><a href="#">CONTACT</a>
  </nav>
</header>

<section class="hero">
  <div class="hero-photo" role="img" aria-label="Street scene of London with a red double-decker bus and Westminster in the background"></div>
  <div class="hero-copy">
    <div class="band"><h1>INTERIM MANAGEMENT</h1></div>
    <p>FOR FUNDS, BROKERS, VENDORS &amp; IT<br>SERVICE PROVIDERS</p>
  </div>
  <div class="hero-dots"><span class="on"></span><span></span><span></span></div>
</section>

<section class="cities">
  <div class="city"><div class="skyline" role="img" aria-label="New York skyline outline"></div><div class="label">NYC</div></div>
  <div class="city"><div class="skyline" role="img" aria-label="Tokyo skyline outline"></div><div class="label">TOKYO</div></div>
  <div class="city"><div class="skyline" role="img" aria-label="Hong Kong skyline outline"></div><div class="label">HONG KONG</div></div>
  <div class="city"><div class="skyline" role="img" aria-label="Singapore skyline outline"></div><div class="label">SINGAPORE</div></div>
</section>

<section class="intro">
  <h2>DEDICATED OURSELVES TO THE<br>PROVISION OF SERVICES</h2>
  <p>Since founding Brightmoor Counsel in 2014 we have dedicated ourselves to the provision of services. What differentiates us from other advisers is our experience as a genuine practitioner in the financial markets. Today's technology allows our clients to take their knowledge to the market in ways that previous generations could only dream of. That is why we are dedicated to helping you choose the right technology strategy, ensuring every investment is made with care.</p>
</section>

<section class="feature" style="height:300px">
  <div class="art" role="img" aria-label="Red gears illustration"></div>
  <div>
    <h3>Process Outsourcing</h3>
    <h4>RFI, RFP &amp; INDEPENDENT TENDER EVALUATIONS<br>( ASSESS BEFORE YOU INVEST )</h4>
    <p>We run structured RFI and RFP processes and independent tender evaluations for trading, market data and risk systems. Our advisers have sat on both sides of the table, so we know which questions matter and which answers to test. Before you commit budget, we score each vendor against your needs, check references, model total cost and give you a clear, written recommendation you can take to the board.</p>
  </div>
</section>

<div class="band-title">OUR CLIENTS</div>
<section class="logo-grid" style="height:300px">
  <div class="logo"><span class="ci"></span>Northgate Capital</div>
  <div class="logo">Keystone Delivery Group</div>
  <div class="logo">Portlane Labs</div>
  <div class="logo"><span class="sq"></span>Cellarway Storage</div>
  <div class="logo"><span class="ci"></span>Quillbrook Systems</div>
  <div class="logo"><span class="sq"></span>Harbourline Data</div>
  <div class="logo">Ferrowell Hosting</div>
</section>

<section class="feature" style="height:280px">
  <div class="art figure" role="img" aria-label="Figure with a red gear illustration"></div>
  <div>
    <h3 class="mifid-title">MiFID II</h3>
    <p class="lines">Brightmoor Counsel can asses your technology, then provide solutions<br>to solve potential issues to get you the correct&nbsp; solution t the correct price point<br>to achive the desired results.</p>
  </div>
</section>

<div class="band-title">OUR PARTNERS</div>
<section class="logo-grid" style="height:320px">
  <div class="logo"><span class="ci"></span>Tidewell Network</div>
  <div class="logo">Keystone Delivery Group</div>
  <div class="logo"><span class="sq"></span>Marlow Carrier</div>
  <div class="logo"><span class="ci"></span>Pacewatch</div>
  <div class="logo"><span class="sq"></span>Arden Services</div>
  <div class="logo">Latchline</div>
  <div class="logo"><span class="ci"></span>Crestpath Networks</div>
</section>

<section class="feature" style="height:320px">
  <div class="art" role="img" aria-label="Red gears illustration"></div>
  <div>
    <h3>Product development</h3>
    <p class="lines">Front – Office Trading Platforms &amp; Market Data<br>Pre&nbsp; | &nbsp;At&nbsp; | &nbsp;Post Trade Risk</p>
  </div>
</section>

<div class="band-title">OUR TEAM</div>
<section class="team">
  <div class="member"><div class="photo" role="img" aria-label="Portrait of Owen Hartley"></div><h5>OWEN HARTLEY</h5><p>Director<br>+44 7700 900 114<br>owen.hartley@brightmoor-counsel.com</p></div>
  <div class="member"><div class="photo" role="img" aria-label="Portrait of Simon Ellery"></div><h5>SIMON ELLERY</h5><p>Director<br>+44 7700 900 362<br>simon.ellery@brightmoor-counsel.com</p></div>
  <div class="member"><div class="photo" role="img" aria-label="Portrait of Clare Whitcombe"></div><h5>CLARE WHITCOMBE</h5><p>Director<br>+44 7700 900 578<br>clare.whitcombe@brightmoor-counsel.com</p></div>
</section>

<footer class="footer">
  <div class="social"><span></span><span></span><span></span></div>
  <nav><span>Home</span><span>What We Do</span><span>How We Do It</span><span>Who Are We</span><span>Why Use Us</span><span>Clients</span><span>Partners</span><span>Contact</span></nav>
  <small>Brightmoor Counsel © 2024 · All rights reserved · Privacy Policy | Terms and Conditions</small>
</footer>

</body>
</html>
```